Postcard for our major fundraising event - KindlingJOY2018

Bright Harbor KIDS Camp (BHK) and Youth Summit Trail Camp (YSTC) are ministries of Lindell Fellowship Church that serve Ventura County children of abuse, abandonment and neglect living in foster care. We are looking for a postcard design to promote our single largest fundraising event of the year, GatheringJOY2018, to raise awareness and support for children of abuse. GatheringJOY is a dinner banquet on at an exclusive outdoor venue, "Willow Hollow" with a rustic, ranch feel and with spectacular panoramic views of the City of Camarillo. The event will include music, refreshments, appetizers, a Santa Maria-style barbeque (BBQ), coffee and dessert, testimonials from camp, prize drawings, an opportunity to partner with BHK and YSTC, and time to socialize before and after.
Updates

I have just uploaded text copy to help designers come closer to what we are looking for. Thank you very much for your interest! -Rob

Target Market(s)

People from both within and from outside our sponsoring church who have a heart for hurting children and who are willing and able to financially support our camping (BHK & YSTC) ministries.

Industry/Entity Type

Church

Font styles to use
Serif
Decorative
Script

Requirements
Must have
• Name: GatheringJOY2018... raising awareness and support for children of abuse
• Date: Thursday, May 24, 2018, 6:30-8:00 pm
• Place: Willow Hollow at Dunmore Ranch, 2715 Barlow Lane, Somis, California.
• Cost: $30 per person
• Tickets: Available at Tixlane.com
• Front side should include the elements of the event (although not necessarily bulleted like below):
• • Social hour
• • Music
• • Hors d’eourves
• • Refreshments
• • Santa Maria-style BBQ dinner
• • Coffee & dessert
• • Prize drawings
• • Stories from camp
• See attachment for suggested copy for back side.
• BHK and YSTC logos should be included on the postcard. I’ve uploaded a variety of photos for the designer to choose from; they do not necessarily all have to be included. There are also lots more pics available on our Facebook (Bright Harbor KIDS of Ventura).
• The front-side of the postcard can be entirely images and text. The back-side of the post card should include our return address at the top left ("BHK/YSTC of Lindell Fellowship Church, 418 Kestrel Ridge Way, Ventura, CA 93017") and should leave at least the right half of the postcard clear for addressing and postage.
• BHK colors are purple (Pantone 267) and red (Pantone 186). YSTC colors are green and yellow.
Nice to have
• A selection of camp photos large enough to easily view, but no so many that they are too small to identify. And, perhaps, a design element that evokes a rustic, outdoors, western, ranch feel, but not so much that it seems that we are promoting a country hoedown.
Should not have
• Anything sexual or sensual, related to alcoholic beverages, gambling, guns, or anything negative.

```html
<!DOCTYPE html>
<html lang="en">
<head>
<meta charset="utf-8">
<title>GatheringJOY2018 Postcard</title>
<link rel="stylesheet" href="https://fonts.googleapis.com/css2?family=Bebas+Neue&family=Source+Sans+3:wght@400;600&family=Montserrat:wght@500;600;700&family=Lora:ital@1&display=swap">
<style>
  :root {
    --purple: #3f2d7c;
    --purple-deep: #2f2166;
    --red: #d12f3a;
    --red-deep: #b8232e;
    --white: #ffffff;
    --ring-gray: #9ea0aa;
    --stage: #e8e8ea;
    --card-back: #f4f4f5;
    --ink: #2b2b33;
    --camp-green: #2e8b3e;
  }
  * { box-sizing: border-box; margin: 0; padding: 0; }
  html, body { width: 1200px; height: 1050px; overflow: hidden; }
  body { background: var(--stage); position: relative; font-family: "Source Sans 3", sans-serif; }

  .postcard {
    position: absolute; left: 232px; width: 735px; height: 490px; overflow: hidden;
    box-shadow: 0 6px 18px rgba(0,0,0,.18);
  }
  .postcard--front { top: 25px; background: var(--purple); }
  .postcard--back { top: 535px; background: var(--card-back); }

  /* front */
  .front-bands { position: absolute; inset: 0; }
  .event-title {
    position: absolute; left: 34px; top: 34px;
    font-family: "Bebas Neue", sans-serif; font-size: 96px; line-height: 1;
    color: var(--white); letter-spacing: 1px;
    -webkit-text-stroke: 3px var(--purple-deep); paint-order: stroke fill;
  }
  .event-year {
    position: absolute; left: 34px; top: 118px;
    font-family: "Bebas Neue", sans-serif; font-size: 96px; line-height: 1; color: var(--purple);
  }
  .event-tagline {
    position: absolute; left: 200px; top: 130px;
    font-family: "Bebas Neue", sans-serif; font-size: 26px; line-height: 26px; color: var(--white);
  }
  .event-when {
    position: absolute; left: 40px; top: 262px;
    font-size: 22px; line-height: 26px; font-weight: 600; color: var(--white);
  }
  .price-box {
    position: absolute; left: 180px; top: 252px; width: 128px; height: 98px;
    background: var(--red); border-radius: 0 0 12px 12px; color: var(--white); text-align: center;
  }
  .price-box .amount { font-size: 60px; font-weight: 600; line-height: 1; margin-top: 8px; display: block; }
  .price-box .unit { font-size: 20px; line-height: 1; display: block; }
  .ticket-pill {
    position: absolute; left: 0; top: 360px; width: 322px; height: 40px;
    background: var(--white); border-radius: 0 20px 20px 0;
    font-size: 23px; font-weight: 600; color: var(--red); line-height: 40px; padding-left: 40px;
  }
  .event-venue {
    position: absolute; left: 40px; top: 414px; width: 300px;
    font-size: 20px; line-height: 26px; color: var(--white);
  }
  .photo { position: absolute; border-radius: 50%; }
  .photo--feature {
    left: 424px; top: 96px; width: 306px; height: 306px; border: 8px solid var(--ring-gray);
    background: radial-gradient(circle at 45% 55%, #c89a68 0%, #7a4a2c 45%, #c8454a 80%, #e9d6c8 100%);
  }
  .photo--small { width: 96px; height: 96px; border: 5px solid var(--red); top: 372px; }
  .photo--music { left: 352px; background: radial-gradient(circle, #b84fbf, #3a1452); }
  .photo--campfire { left: 448px; background: radial-gradient(circle at 60% 70%, #e88a3a, #3c1e12 70%); }
  .photo--appetizers { left: 544px; background: radial-gradient(circle, #f1e3c4, #7fae5a 80%); }

  /* back */
  .partner-row { position: absolute; left: 30px; top: 24px; display: flex; align-items: center; gap: 34px; }
  .partner { display: flex; align-items: center; gap: 8px; font-family: "Montserrat", sans-serif; font-weight: 700; font-size: 18px; }
  .partner--trail { color: var(--camp-green); }
  .partner--trail .dot { width: 34px; height: 34px; border-radius: 50%; background: var(--camp-green); }
  .partner--kids { color: var(--purple); }
  .host-line {
    position: absolute; left: 30px; top: 76px; width: 420px;
    font-family: "Montserrat", sans-serif; font-weight: 600; font-size: 12.5px; line-height: 16px; color: var(--red);
  }
  .invite-detail {
    position: absolute; left: 62px; top: 168px; width: 310px; height: 126px;
    background: var(--red); border-radius: 0 0 22px 22px; padding-top: 30px;
    font-family: "Montserrat", sans-serif; font-size: 12.5px; line-height: 16px; color: var(--white); text-align: center;
  }
  .invite-box {
    position: absolute; left: 30px; top: 112px; width: 374px; height: 76px;
    background: var(--purple); border-radius: 18px; color: var(--white); text-align: center;
    font-family: "Montserrat", sans-serif;
  }
  .invite-box .lead { font-size: 12.5px; margin-top: 6px; display: block; }
  .invite-box .name { font-size: 30px; font-weight: 700; line-height: 32px; display: block; letter-spacing: .5px; }
  .invite-box .tagline { font-family: "Lora", serif; font-style: italic; font-size: 12px; display: block; }
  .ticket-info {
    position: absolute; left: 30px; top: 312px; width: 420px;
    font-family: "Montserrat", sans-serif; color: var(--ink);
  }
  .ticket-info .headline { font-size: 15px; font-weight: 700; line-height: 18px; }
  .ticket-info .note { font-size: 10.5px; font-weight: 500; line-height: 14px; }
  .contact-info {
    position: absolute; left: 30px; top: 372px; width: 440px;
    font-family: "Montserrat", sans-serif; font-size: 10.5px; font-weight: 600; line-height: 15px; color: var(--ink);
  }
  .contact-info .label { display: block; text-align: center; font-weight: 500; }
  .address-lines { position: absolute; left: 470px; top: 200px; width: 240px; }
  .address-lines span { display: block; height: 1.5px; background: var(--ink); margin-bottom: 40px; }
</style>
</head>
<body>

<section class="postcard postcard--front" aria-label="Postcard front">
  <svg class="front-bands" viewBox="0 0 735 490" preserveAspectRatio="none" aria-hidden="true">
    <defs>
      <linearGradient id="redBand" x1="0" y1="0" x2="1" y2="1">
        <stop offset="0" stop-color="#b8232e"/>
        <stop offset="1" stop-color="#de4048"/>
      </linearGradient>
      <linearGradient id="purpleBand" x1="0" y1="0" x2="0" y2="1">
        <stop offset="0" stop-color="#3f2d7c"/>
        <stop offset="1" stop-color="#4c3a8e"/>
      </linearGradient>
    </defs>
    <rect width="735" height="490" fill="url(#purpleBand)"/>
    <path d="M0,0 H735 V40 C430,250 160,270 0,212 Z" fill="#ffffff"/>
    <path d="M0,0 H735 V22 C430,232 160,252 0,196 Z" fill="url(#redBand)"/>
  </svg>

  <h1 class="event-title">GATHERING JOY</h1>
  <div class="event-year">2018</div>
  <p class="event-tagline">Raising awareness<br>&amp; support for<br>children of abuse</p>

  <div class="photo photo--feature" role="img" aria-label="Photo of a slice of dessert with a cup of coffee"></div>
  <div class="photo photo--small photo--music" role="img" aria-label="Photo of live music on stage"></div>
  <div class="photo photo--small photo--campfire" role="img" aria-label="Photo of a camp gathering around a fire"></div>
  <div class="photo photo--small photo--appetizers" role="img" aria-label="Photo of appetizers on a plate"></div>

  <p class="event-when">THURSDAY<br>May 24, 2018<br>6:30-8:00 pm</p>
  <div class="price-box"><span class="amount">$30</span><span class="unit">per person</span></div>
  <div class="ticket-pill">Available at Tixlane.com</div>
  <p class="event-venue">Willow Hollow at Dunmore Ranch,<br>2715 Barlow Lane, Somis, California.</p>
</section>

<section class="postcard postcard--back" aria-label="Postcard back">
  <div class="partner-row">
    <div class="partner partner--trail"><span class="dot"></span>YSTC</div>
    <div class="partner partner--kids">Bright Harbor KIDS</div>
  </div>
  <p class="host-line">Bright Harbor KIDS Camp &amp; Youth Summit Trail Camp<br>of Lindell Fellowship Church</p>

  <div class="invite-detail">
    at the exclusive<br>Willow Hollow at Dunmore Ranch<br>2715 Barlow Lane, Somis, CA<br>on<br>Thursday, May 24, 2018<br>6:30-8:00pm
  </div>
  <div class="invite-box">
    <span class="lead">invite you to join us for</span>
    <span class="name">GatheringJOY2018</span>
    <span class="tagline">raising awareness &amp; support for children of abuse</span>
  </div>

  <div class="ticket-info">
    <p class="headline">Tickets $30 per person/Available at Tixlane.com</p>
    <p class="note">All proceeds to benefit BHKC &amp; YSTC serving children of abuse ages 7-14.</p>
  </div>
  <div class="contact-info">
    <span class="label">For more information:</span>
    BHKC: Director Rob Ashford (805) 555-0142 / bhkventura@lindellmail.net<br>
    YSTC: Director Dale Ferris (805) 555-0187 / trailcamp.director@lindellmail.net
  </div>

  <div class="address-lines" aria-hidden="true"><span></span><span></span><span></span></div>
</section>

</body>
</html>
```